Business Card Design Project

I have established a company called "Corvella" which is a business specialising in psychotherapy/counselling , predominantly for anxiety & depression.

My name is Nel....hence, the Corvella link. However, Corvella was also chosen for its reference to green shoots of growth/recovery.

Corvella is to be "upmarket" and highly professional. I'm keen for the style and colours to reflect this.....taupe/grey with navy/black script, for example.....NO primary colours.

My name needs to be on the card and my mobile number. Not sure, but suspect it should also have my qualifications ( BA (Psych) & BSc (Hons) Psychology). Mobile number 0412 903 618.

```html
<!DOCTYPE html>
<html lang="en">
<head>
<meta charset="utf-8">
<title>Corvella business card</title>
<link rel="stylesheet" href="https://fonts.googleapis.com/css2?family=Lato:wght@300;400;700;900&display=swap">
<style>
  :root {
    --bg: #3a3937;
    --ivory: #f6f3ee;
    --taupe-light: #ddd4c8;
    --taupe: #bfb2a3;
    --taupe-deep: #a39584;
    --stone: #9b968f;
    --sage: #7d8c64;
    --sage-light: #aab593;
    --navy: #1f2a44;
    --ink: #222327;
    --paper: #f6f3ee;
  }
  * { margin: 0; padding: 0; box-sizing: border-box; }
  html, body {
    width: 1200px; height: 1018px; overflow: hidden;
    background: var(--bg);
    font-family: "Lato", Arial, sans-serif;
  }
  .canvas { position: relative; width: 1200px; height: 1018px; }
  .card {
    position: absolute; width: 620px; height: 420px; overflow: hidden;
  }
  .card--front {
    left: 60px; top: 70px;
    background: linear-gradient(90deg, var(--ivory) 0%, var(--taupe-light) 30%, var(--taupe) 62%, var(--stone) 100%);
  }
  .card--back {
    left: 520px; top: 530px;
    background: linear-gradient(90deg, var(--stone) 0%, var(--taupe) 35%, var(--taupe-light) 70%, var(--ivory) 100%);
  }
  .plant { position: absolute; }
  .card--front .plant { left: 0; top: 0; width: 170px; height: 330px; }
  .card--back .plant { left: 110px; top: 50px; width: 380px; height: 110px; }
  .stem-band {
    position: absolute; left: 60px; top: 278px; width: 560px; height: 22px;
  }
  .identity {
    position: absolute; right: 40px; top: 48px; text-align: right;
  }
  .identity__name {
    font-weight: 300; font-size: 62px; line-height: 1; color: var(--navy);
    letter-spacing: 1px;
  }
  .identity__brand {
    font-weight: 400; font-size: 34px; line-height: 1.1; color: var(--sage);
  }
  .identity__details {
    margin-top: 14px; list-style: none;
    font-size: 21px; line-height: 1.3; color: var(--ink);
  }
  .tagline-band {
    position: absolute; left: 190px; right: 0; top: 338px; height: 56px;
    background: var(--navy);
    display: flex; align-items: center; padding-left: 22px;
  }
  .tagline {
    font-size: 27px; font-weight: 400; color: var(--paper);
  }
  .back-copy {
    position: absolute; left: 70px; top: 175px; width: 520px;
  }
  .back-copy__lead {
    font-weight: 900; font-size: 34px; color: var(--navy);
  }
  .back-copy__focus {
    margin-top: 10px; padding-left: 40px;
    font-weight: 900; font-size: 31px; line-height: 1.25; color: var(--ink);
  }
</style>
</head>
<body>
<main class="canvas">
  <section class="card card--front" aria-label="Card front">
    <svg class="plant" viewBox="0 0 170 330" role="img" aria-label="Green shoot illustration rising from the left edge">
      <defs>
        <linearGradient id="plant-fill" x1="0" y1="0" x2="1" y2="1">
          <stop offset="0" stop-color="#aab593"/>
          <stop offset="1" stop-color="#7d8c64"/>
        </linearGradient>
      </defs>
      <rect x="0" y="0" width="170" height="330" rx="40" fill="url(#plant-fill)"/>
    </svg>
    <svg class="stem-band" viewBox="0 0 560 22" preserveAspectRatio="none" aria-hidden="true">
      <rect x="0" y="0" width="560" height="22" rx="6" fill="#7d8c64"/>
    </svg>
    <div class="identity">
      <div class="identity__name">NEL</div>
      <div class="identity__brand">Corvella</div>
      <ul class="identity__details">
        <li>BA (Psych)</li>
        <li>BSc (Hons) Psychology</li>
        <li>Mobile: 0412 903 618</li>
      </ul>
    </div>
    <div class="tagline-band"><p class="tagline">specialising in psychotherapy</p></div>
  </section>

  <section class="card card--back" aria-label="Card back">
    <svg class="plant" viewBox="0 0 380 110" preserveAspectRatio="none" role="img" aria-label="Green leaf sweep illustration">
      <defs>
        <linearGradient id="leaf-fill" x1="0" y1="1" x2="1" y2="0">
          <stop offset="0" stop-color="#7d8c64"/>
          <stop offset="1" stop-color="#aab593"/>
        </linearGradient>
      </defs>
      <rect x="0" y="0" width="380" height="110" rx="50" fill="url(#leaf-fill)"/>
    </svg>
    <div class="back-copy">
      <p class="back-copy__lead">specialising in psychotherapy</p>
      <p class="back-copy__focus">predominantly for anxiety<br>&amp; depression.</p>
    </div>
  </section>
</main>
</body>
</html>
```